Boutique Technology Consultancy specialising is Electronic and physical security

We need to redo our existing outdated website. For your reference the link www.pelu.com.au

```html
<!DOCTYPE html>
<html lang="en">
<head>
<meta charset="utf-8">
<title>PELU Services — Electronic and Physical Security</title>
<link rel="stylesheet" href="https://fonts.googleapis.com/css2?family=Libre+Baskerville:wght@400;700&family=Poppins:wght@700;800&family=Lato:wght@400;700;900&display=swap">
<style>
:root{
  --maroon:#6b1c14;
  --maroon-deep:#4a120d;
  --brick:#8c2619;
  --accent:#c8402f;
  --ink:#222;
  --muted:#777;
  --paper:#ffffff;
  --mist:#f6f6f6;
  --night:#050505;
}
*{box-sizing:border-box;margin:0;padding:0}
html,body{width:1200px;height:4365px;overflow:hidden}
body{position:relative;background:var(--paper);font-family:"Lato",sans-serif;color:var(--ink)}
.abs{position:absolute}
.serif{font-family:"Libre Baskerville",serif}
.btn{position:absolute;display:flex;align-items:center;justify-content:center;gap:10px;background:var(--brick);color:#fff;border-radius:26px;font-size:14px;font-family:"Lato",sans-serif}
.btn svg{width:16px;height:12px}
.photo{position:absolute}

/* top bar */
.topbar{left:30px;top:0;width:1140px;height:59px;background:var(--maroon);border-radius:0 0 22px 22px;color:#fff;font-size:13px;z-index:3}
.topbar .item{position:absolute;top:20px;display:flex;align-items:center;gap:12px}
.dots{position:absolute;right:22px;top:16px;display:flex;gap:12px}
.dots span{width:26px;height:26px;border-radius:50%;background:#fff;opacity:.9}

/* hero */
.hero{left:0;top:0;width:1200px;height:737px;overflow:hidden}
.hero .photo{inset:0;background:linear-gradient(120deg,#8a5a49 0%,#6d3328 40%,#5b1f17 70%,#4b1610 100%)}
.brand{position:absolute;display:flex;align-items:center;gap:8px;font-family:"Lato",sans-serif;font-weight:900;color:#fff;letter-spacing:1px}
.brand i{display:block;border-radius:2px;background:var(--accent)}
.nav{position:absolute;left:378px;top:103px;display:flex;gap:22px;color:#fff;font-size:14px}
.hero-label{position:absolute;left:0;width:1200px;top:259px;text-align:center;color:#fff;font-size:12px;letter-spacing:2px;font-weight:700}
.hero-title{position:absolute;left:0;width:1200px;top:292px;text-align:center;color:#fff;font-family:"Poppins",sans-serif;font-weight:800;font-size:60px;line-height:68px}
.hero-title em{font-style:normal;color:#7a1a10}
.hero-sub{position:absolute;left:0;width:1200px;top:453px;text-align:center;color:#fff;font-size:15px}

/* services intro */
.intro-h{left:47px;top:842px;font-size:32px;color:var(--maroon)}
.intro-p{left:47px;top:902px;width:540px;font-size:14px;line-height:26px;color:var(--muted)}
.focus{left:629px;top:775px;width:523px;height:280px;background:var(--maroon);border-radius:22px;padding:40px 48px}
.focus li{list-style:none;display:flex;align-items:center;gap:24px;color:#fff;font-family:"Libre Baskerville",serif;font-weight:700;font-size:16px;height:73px}

/* experience band */
.band{left:0;top:1152px;width:1200px;height:518px;background:linear-gradient(115deg,#3c2a2a 0%,#4e2b24 45%,#6a3a22 70%,#3a1c18 100%)}
.eyebrow{font-size:11px;letter-spacing:2px;font-weight:700;text-transform:uppercase}
.card{position:absolute;top:1419px;width:258px;height:332px;background:#fff;border-radius:22px;text-align:center;padding-top:36px;box-shadow:0 8px 24px rgba(0,0,0,.06)}
.card svg.ic{width:46px;height:46px}
.card h3{font-family:"Libre Baskerville",serif;font-weight:400;font-size:17px;line-height:23px;margin-top:18px;color:#222}
.card p{font-size:14px;line-height:25px;color:var(--muted);margin-top:8px;padding:0 36px}
.card .btn{left:50%;transform:translateX(-50%);width:154px;height:47px;bottom:34px}
.card.hot{background:var(--maroon);height:307px}
.card.hot h3,.card.hot p{color:#fff}
.card.hot .btn{background:var(--accent);bottom:34px}

/* offer */
.offer-bg{left:0;top:1780px;width:1200px;height:1152px;background:var(--mist)}
.offer-img{left:208px;top:1861px;width:275px;height:348px;background:linear-gradient(160deg,#c49a5a 0%,#8fa36a 35%,#d8c7b4 60%,#9cb7cf 100%)}
.offer-h{left:512px;top:1925px;font-size:42px;line-height:52px;color:var(--maroon)}
.offer-p{left:512px;top:2048px;width:440px;font-size:14px;line-height:26px;color:var(--muted)}

/* projects */
.proj-h{left:90px;top:2352px;font-size:33px;line-height:42px;color:var(--maroon)}
.proj{position:absolute;top:2476px;width:320px;height:346px;border-radius:18px;overflow:hidden;color:#fff}
.proj .photo{inset:0}
.proj .txt{position:absolute;left:47px;top:138px;width:240px}
.proj h4{font-family:"Libre Baskerville",serif;font-weight:400;font-size:17px}
.proj p{font-size:14px;line-height:26px;margin-top:6px}

/* cta */
.cta{left:0;top:2932px;width:1200px;height:429px;background:linear-gradient(110deg,#4a1a15 0%,#5c1f18 45%,#6b2a22 75%,#7a4632 100%)}
.cta-h{left:0;width:1200px;top:3066px;text-align:center;font-size:58px;line-height:68px;color:#fff}

/* team */
.member{position:absolute;top:3470px;width:247px;height:332px;border-radius:18px;overflow:hidden}
.member .photo{inset:0}
.member .cover{position:absolute;inset:0;background:rgba(107,28,20,.82);color:#fff;text-align:center}

/* footer */
.footer{left:0;top:3912px;width:1200px;height:453px;background:var(--night);color:#fff}
.footer .col-h{font-family:"Libre Baskerville",serif;font-size:22px}
.footer .link{position:absolute;font-size:15px}
.contact{display:flex;align-items:center;gap:10px}
</style>
</head>
<body>

<!-- hero -->
<section class="abs hero">
  <div class="photo" role="img" aria-label="Woman working at a desk beside a large window in warm light"></div>
  <svg class="abs" style="left:0;top:0" width="1200" height="737" viewBox="0 0 1200 737">
    <polygon points="0,737 1200,560 1200,737" fill="var(--maroon)"/>
    <polygon points="0,732 1200,556 1200,566 0,742" fill="#fff"/>
  </svg>
  <div class="brand" style="left:50px;top:96px;font-size:30px"><i style="width:20px;height:20px"></i>PELU</div>
  <nav class="nav"><span>Home</span><span>Experience</span><span>Services</span><span>Team</span><span>About</span><span>Contact</span></nav>
  <div class="btn" style="left:992px;top:89px;width:153px;height:46px;background:var(--accent);font-size:15px">Get A Quote</div>
  <div class="hero-label">ELECTRONIC AND PHYSICAL SECURITY</div>
  <h1 class="hero-title">YOUR TECHNOLOGY<br>PROJECTS <em>MADE EASY.</em></h1>
  <p class="hero-sub">We provide technology consulting services to corporate and government clients</p>
</section>

<header class="abs topbar">
  <div class="item" style="left:40px">
    <svg width="16" height="18" viewBox="0 0 16 18" fill="none" stroke="#fff" stroke-width="1.5"><path d="M8 17s6-6 6-10A6 6 0 0 0 2 7c0 4 6 10 6 10z"/><circle cx="8" cy="7" r="2"/></svg>
    SOUTHBANK VIC 3006
  </div>
  <div class="item" style="left:272px">
    <svg width="18" height="18" viewBox="0 0 24 24" fill="none" stroke="#fff" stroke-width="1.6"><path d="M5 3h4l2 5-3 2a11 11 0 0 0 6 6l2-3 5 2v4a2 2 0 0 1-2 2A17 17 0 0 1 3 5a2 2 0 0 1 2-2z"/></svg>
    1300 555 014
  </div>
  <div class="dots"><span></span><span></span><span></span></div>
</header>

<!-- services intro -->
<h2 class="abs serif intro-h">PELU Services</h2>
<p class="abs intro-p">PELU Services was established in 2016 by Tom Harlow to provide technology consulting services to corporate and government clients with a focus on:</p>
<div class="btn" style="left:47px;top:984px;width:170px;height:47px">Learn More <svg viewBox="0 0 16 12" fill="none" stroke="#fff" stroke-width="1.5"><path d="M1 6h13M9 1l5 5-5 5"/></svg></div>
<ul class="abs focus">
  <li><svg width="30" height="22" viewBox="0 0 30 22" fill="none" stroke="var(--accent)" stroke-width="4"><path d="M2 11l9 8L28 2"/></svg>Property/Facilities Management</li>
  <li><svg width="30" height="22" viewBox="0 0 30 22" fill="none" stroke="var(--accent)" stroke-width="4"><path d="M2 11l9 8L28 2"/></svg>Asset Management</li>
  <li><svg width="30" height="22" viewBox="0 0 30 22" fill="none" stroke="var(--accent)" stroke-width="4"><path d="M2 11l9 8L28 2"/></svg>Development And Construction</li>
</ul>

<!-- experience band -->
<section class="abs band" role="img" aria-label="Looking up at glass office towers with a warm sun flare"></section>
<div class="abs eyebrow" style="left:0;width:1200px;top:1247px;text-align:center;color:var(--accent)">EXPERIENCE</div>
<h2 class="abs serif" style="left:0;width:1200px;top:1280px;text-align:center;color:#fff;font-size:32px;line-height:41px;font-weight:400">PELU Has A Diverse Range Of Project<br>Experience</h2>

<div class="card" style="left:42px">
  <svg class="ic" viewBox="0 0 46 46" fill="none" stroke="var(--maroon)" stroke-width="1.6"><rect x="6" y="10" width="26" height="18" rx="2"/><path d="M2 32h34"/><rect x="30" y="16" width="12" height="20" rx="2"/></svg>
  <h3>Technology<br>Roadmaps</h3>
  <p>Lorem ipsum dolor sit amet consectetur adipiscing elit.</p>
  <div class="btn">Learn More <svg viewBox="0 0 16 12" fill="none" stroke="#fff" stroke-width="1.5"><path d="M1 6h13M9 1l5 5-5 5"/></svg></div>
</div>
<div class="card hot" style="left:329px">
  <svg class="ic" viewBox="0 0 46 46" fill="none" stroke="var(--accent)" stroke-width="1.6"><rect x="3" y="6" width="26" height="18" rx="2"/><path d="M8 24v7l6-7"/><rect x="18" y="18" width="24" height="16" rx="2"/><path d="M36 34v6l-6-6M8 12h16M8 17h10M23 24h14M23 28h10"/></svg>
  <h3>Asset Management<br>Plans</h3>
  <p>Lorem ipsum dolor sit amet consectetur</p>
  <div class="btn">Learn More <svg viewBox="0 0 16 12" fill="none" stroke="#fff" stroke-width="1.5"><path d="M1 6h13M9 1l5 5-5 5"/></svg></div>
</div>
<div class="card" style="left:614px">
  <svg class="ic" viewBox="0 0 46 46" fill="none" stroke="var(--maroon)" stroke-width="1.6"><circle cx="21" cy="25" r="16"/><path d="M21 25V9M21 25l12 10"/><path d="M26 4a16 16 0 0 1 14 14H26z"/></svg>
  <h3>Projects Design &amp;<br>Procurement</h3>
  <p>Lorem ipsum dolor sit amet consectetur adipiscing elit.</p>
  <div class="btn">Learn More <svg viewBox="0 0 16 12" fill="none" stroke="#fff" stroke-width="1.5"><path d="M1 6h13M9 1l5 5-5 5"/></svg></div>
</div>
<div class="card" style="left:898px">
  <svg class="ic" viewBox="0 0 46 46" fill="none" stroke="var(--maroon)" stroke-width="1.6"><rect x="6" y="6" width="26" height="34" rx="2"/><path d="M11 14h14M11 20h10M11 32h8"/><path d="M40 8l-16 16-3 7 7-3L44 12z"/></svg>
  <h3>Operations And<br>Maintenance</h3>
  <p>Lorem ipsum dolor sit amet consectetur adipiscing elit.</p>
  <div class="btn">Learn More <svg viewBox="0 0 16 12" fill="none" stroke="#fff" stroke-width="1.5"><path d="M1 6h13M9 1l5 5-5 5"/></svg></div>
</div>

<!-- offer -->
<div class="abs offer-bg"></div>
<div class="abs offer-img photo" role="img" aria-label="Smiling consultant seated at a desk with a laptop"></div>
<div class="abs eyebrow" style="left:512px;top:1892px;color:var(--maroon)">PELU SERVICES</div>
<h2 class="abs serif offer-h" style="font-weight:400">We Offer End To End<br>Services</h2>
<p class="abs offer-p">PELU Services provides independent professional services for projects as well as operations and maintenance.</p>
<div class="btn" style="left:512px;top:2133px;width:168px;height:47px">Learn More <svg viewBox="0 0 16 12" fill="none" stroke="#fff" stroke-width="1.5"><path d="M1 6h13M9 1l5 5-5 5"/></svg></div>

<!-- projects -->
<div class="abs eyebrow" style="left:90px;top:2320px;color:var(--maroon)">EXPERIENCE</div>
<h2 class="abs serif proj-h" style="font-weight:400">PELU Has A Diverse Range Of Project<br>Experience.</h2>
<div class="btn" style="left:944px;top:2353px;width:166px;height:46px">View More <svg viewBox="0 0 16 12" fill="none" stroke="#fff" stroke-width="1.5"><path d="M1 6h13M9 1l5 5-5 5"/></svg></div>

<div class="proj" style="left:90px">
  <div class="photo" role="img" aria-label="Overhead motorway gantry against a cloudy sky, sepia tone" style="background:linear-gradient(180deg,#8a8280 0%,#5a4a48 55%,#3c2826 100%)"></div>
  <div class="txt"><h4>Northway Link</h4><p>Virtual servers, network and CCTV upgrade design and project management for this landmark road transportation Public Private Partnership (PPP).</p></div>
</div>
<div class="proj" style="left:439px">
  <div class="photo" role="img" aria-label="Glass dome roof of a shopping centre, sepia tone" style="background:linear-gradient(180deg,#4a3836 0%,#6a5654 50%,#3a2624 100%)"></div>
  <div class="txt"><h4>Central Arcade</h4><p>Security technology design consulting for this popular retail and entertainment hub which is managed by the Meridian Group.</p></div>
</div>
<div class="proj" style="left:788px">
  <div class="photo" role="img" aria-label="Twin glass office towers rising into the sky, sepia tone" style="background:linear-gradient(180deg,#9a8e8c 0%,#5e4a48 50%,#35221f 100%)"></div>
  <div class="txt"><h4>Harbour Towers</h4><p>Shared building network and security systems integration consulting for this iconic office tower which is managed by Crestline.</p></div>
</div>

<!-- cta -->
<section class="abs cta" role="img" aria-label="Desk with a laptop and a pot of pencils in a bright office"></section>
<div class="abs eyebrow" style="left:0;width:1200px;top:3030px;text-align:center;color:var(--accent);font-weight:400">COMMITTED TO A RANGE OF SOCIAL INITIATIVES.</div>
<h2 class="abs serif cta-h" style="font-weight:400">PELU Seeks To Make The<br>World A Better Place.</h2>
<div class="btn" style="left:497px;top:3220px;width:205px;height:46px">Get A Quotation <svg viewBox="0 0 16 12" fill="none" stroke="#fff" stroke-width="1.5"><path d="M1 6h13M9 1l5 5-5 5"/></svg></div>

<!-- team -->
<div class="member" style="left:63px">
  <div class="photo" role="img" aria-label="Portrait of team member" style="background:linear-gradient(180deg,#8a5a44,#5a3226)"></div>
  <div class="cover">
    <div class="serif" style="margin-top:98px;font-size:22px">Jane Doe</div>
    <div class="eyebrow" style="margin-top:10px;color:var(--accent);font-weight:400">DESIGNER</div>
    <div style="display:flex;gap:18px;justify-content:center;margin-top:26px">
      <span style="width:34px;height:34px;border-radius:50%;background:var(--accent)"></span>
      <span style="width:34px;height:34px;border-radius:50%;background:var(--accent)"></span>
      <span style="width:34px;height:34px;border-radius:50%;background:var(--accent)"></span>
    </div>
  </div>
</div>
<div class="member" style="left:339px"><div class="photo" role="img" aria-label="Portrait of team member" style="background:linear-gradient(180deg,#8c7a52,#c9b8a6 50%,#4a4a52)"></div></div>
<div class="member" style="left:614px"><div class="photo" role="img" aria-label="Portrait of team member" style="background:linear-gradient(180deg,#3a3a3a,#8a6e5e 50%,#2a2e38)"></div></div>
<div class="member" style="left:890px"><div class="photo" role="img" aria-label="Portrait of team member" style="background:linear-gradient(180deg,#e6e6e6,#c9a890 50%,#d8d8dc)"></div></div>

<!-- footer -->
<footer class="abs footer">
  <div class="brand" style="left:57px;top:114px;font-size:40px"><i style="width:26px;height:26px"></i>PELU</div>
  <p class="abs" style="left:57px;top:182px;width:400px;font-size:15px;line-height:26px">PELU seeks to make the world a better place and is committed to a range of social initiatives.</p>

  <div class="abs col-h" style="left:610px;top:104px">Quick Links</div>
  <span class="link" style="left:610px;top:155px">Expertise</span>
  <span class="link" style="left:610px;top:196px">Services</span>
  <span class="link" style="left:610px;top:235px">Team</span>
  <span class="link" style="left:610px;top:276px">Contact Us</span>

  <div class="abs serif" style="left:885px;top:112px;font-size:17px">Head Office</div>
  <p class="abs" style="left:885px;top:146px;width:260px;font-size:15px;line-height:27px">PO Box 1420 SOUTHBANK VIC 3006</p>
  <div class="abs contact" style="left:885px;top:232px;font-size:15px">
    <svg width="18" height="16" viewBox="0 0 18 16" fill="none" stroke="#fff" stroke-width="1.4"><rect x="1" y="2" width="16" height="12" rx="1"/><path d="M1 3l8 6 8-6"/></svg>hello@pelu.com.au</div>
  <div class="abs contact" style="left:885px;top:272px;font-size:15px">
    <svg width="18" height="18" viewBox="0 0 24 24" fill="none" stroke="#fff" stroke-width="1.6"><path d="M5 3h4l2 5-3 2a11 11 0 0 0 6 6l2-3 5 2v4a2 2 0 0 1-2 2A17 17 0 0 1 3 5a2 2 0 0 1 2-2z"/></svg>1300 555 014</div>

  <div class="abs" style="left:47px;top:364px;width:1106px;height:1px;background:#2a2a2a"></div>
  <div class="abs eyebrow" style="left:47px;top:403px">ALLRIGHT RESERVED - PELU</div>
  <div class="abs" style="right:47px;top:398px;display:flex;gap:14px">
    <span style="width:28px;height:28px;border-radius:50%;background:#fff"></span>
    <span style="width:28px;height:28px;border-radius:50%;background:#fff"></span>
    <span style="width:28px;height:28px;border-radius:50%;background:#fff"></span>
  </div>
</footer>

</body>
</html>
```